Shopify Web-Page "Tiny-ThreadDays

We are building a new business in Switzerland offering premium sewing holiday camps for kids aged 9–14. In enclosed brief outlines our requirements for a complete Shopify homepage design and a multilingual logo creation.
Domains: tiny-threaddays.ch ; tiny-giornifilo.ch ; tiny-fadentage.ch

Project Overview
We are looking for:
1. A modern, fully designed Shopify homepage in English using standard Shopify content blocks (no custom coding), which we can later update ourselves. Supporting Multilanguage (EN, German, Italian).

2. A logo design that includes the brand identity and communicates our multilingual, creative, and child-focused positioning.

All details in enclosed

```html
<!DOCTYPE html>
<html lang="en">
<head>
<meta charset="utf-8">
<title>Tiny-ThreadDays – Creative Sewing Holidays for Kids</title>
<link href="https://fonts.googleapis.com/css2?family=Baloo+2:wght@600;700;800&family=Poppins:wght@400;500;600;700&display=swap" rel="stylesheet">
<style>
:root{
  --pink:#e8507a;
  --pink-soft:#fbe3ea;
  --yellow:#f2b51c;
  --orange:#f5a623;
  --blue:#2aa8dc;
  --blue-label:#2b9fd3;
  --sky:#e9f5fb;
  --cta:#3db4e2;
  --ink:#222;
  --muted:#666;
  --night:#3a2a6c;
  --line:#e6e6e6;
}
*{box-sizing:border-box;margin:0;padding:0}
html,body{width:1200px;height:5029px;overflow:hidden}
body{position:relative;font-family:"Poppins",sans-serif;color:var(--ink);background:#fff}
.abs{position:absolute}
svg{display:block}

/* top bar */
.topbar{left:0;top:0;width:1200px;height:39px;background:var(--orange);font-size:13px;color:#222}
.topbar span{position:absolute;top:10px;display:flex;align-items:center;gap:6px}
/* nav */
.nav{left:0;top:39px;width:1200px;height:74px;background:#fff}
.brand{left:140px;top:23px;width:106px;height:106px;background:var(--pink);border:3px solid #f48aa6;display:flex;align-items:center;justify-content:center;text-align:center;font-family:"Poppins",sans-serif;font-weight:700;color:#fff;font-size:15px;line-height:1.15;z-index:5}
.menu a{position:absolute;top:70px;font-size:12.5px;font-weight:500;color:#333;text-decoration:none}
.menu a.active{color:var(--pink)}
.btn-book{left:964px;top:59px;width:94px;height:37px;background:var(--pink);color:#fff;font-size:13px;display:flex;align-items:center;justify-content:center;border-radius:3px}

/* hero */
.hero-photo{left:0;top:113px;width:1200px;height:576px;background:linear-gradient(100deg,#5a4a45 0%,#7b6a62 35%,#a48c7e 60%,#6d6a72 100%)}
.hero-box{left:146px;top:240px;width:449px;height:322px;background:rgba(35,30,32,.72)}
.hero-box h1{position:absolute;left:24px;top:40px;font-family:"Baloo 2",sans-serif;font-weight:700;font-size:49px;line-height:60px;color:#fff}
.hero-box p{position:absolute;left:24px;top:163px;width:420px;font-size:15.5px;line-height:24px;color:#fff}
.hero-btn{position:absolute;left:24px;top:234px;width:193px;height:36px;background:var(--pink);color:#fff;font-size:14px;display:flex;align-items:center;justify-content:center}
.scroll-dot{left:561px;top:652px;width:78px;height:78px;border-radius:50%;background:#fff;box-shadow:0 3px 10px rgba(0,0,0,.12);display:flex;align-items:center;justify-content:center}

/* section labels */
.label{font-size:14px;font-weight:600;color:var(--blue-label);text-transform:uppercase;letter-spacing:.3px}
.heading{font-size:26px;font-weight:500;text-transform:uppercase;color:#222}
.heading em{font-style:normal;color:var(--pink);font-weight:600;border-bottom:3px solid var(--yellow);padding-bottom:1px}
.center{left:0;width:1200px;text-align:center}

/* about */
.about-text{left:599px;top:812px;width:462px}
.about-text .heading{margin-top:12px;font-size:25px}
.about-text p{font-size:12.3px;line-height:21.5px;color:#444;margin-top:14px}
.person{position:absolute;top:1118px;display:flex;align-items:center;gap:18px}
.person .avatar{width:68px;height:68px;border-radius:50%;background:linear-gradient(160deg,#d8cfc8,#7a6a62)}
.person b{display:block;font-size:16px;font-weight:600}
.person small{font-size:13px;color:#444}

/* how */
.how-cards{left:140px;top:1526px;width:920px;height:207px;display:flex;gap:17px}
.how-card{flex:1;min-width:0;background:#fff;border-radius:6px;padding:18px 14px;position:relative;box-shadow:0 2px 8px rgba(0,0,0,.04)}
.how-card .num{position:absolute;right:14px;top:8px;font-size:44px;font-weight:700;color:#f1f1f1;line-height:1.1}
.how-card .step-icon{position:absolute;left:14px;top:18px}
.how-card h3{position:relative;margin-top:60px;font-size:13.5px;font-weight:500;white-space:nowrap}
.how-card p{position:relative;margin-top:4px;font-size:12px;line-height:19px;color:#666}

/* why */
.why-item{position:absolute;display:flex;align-items:center;gap:18px;font-size:13.5px;line-height:23px;color:#333}
.why-item.left{text-align:right}
.ico{width:70px;height:70px;border-radius:50%;display:flex;align-items:center;justify-content:center;flex:none}
.ico.y{background:var(--yellow)}.ico.b{background:var(--blue)}.ico.p{background:var(--pink)}
.why-ring{left:449px;top:2056px;width:302px;height:302px;border-radius:50%;border:2px dashed #888}
.why-core{left:475px;top:2082px;width:250px;height:250px;border-radius:50%;background:#fff;box-shadow:0 4px 20px rgba(0,0,0,.1);display:flex;align-items:center;justify-content:center;font-weight:700;font-size:28px;color:var(--pink);text-align:center;line-height:1.1}
.divider{left:140px;top:2449px;width:920px;height:1px;background:var(--line)}

/* camps */
.camp{position:absolute;top:2614px;width:283px;height:371px;background:#fff;border-radius:6px;box-shadow:0 2px 12px rgba(0,0,0,.09);overflow:hidden}
.camp .pic{height:160px}
.camp h3{margin:16px 16px 0;font-size:14px;font-weight:500}
.camp p{margin:8px 16px 0;font-size:12px;line-height:20.5px;color:#666;height:84px}
.camp dl{margin:16px 16px 0;display:grid;grid-template-columns:auto 1fr auto auto;column-gap:10px;row-gap:14px;font-size:12px}
.camp dt{font-weight:600}.camp dd{color:#666}
.pill{height:42px;border-radius:21px;display:flex;align-items:center;gap:14px;padding:0 6px 0 18px;font-size:14px}
.pill i{width:30px;height:30px;border-radius:50%;display:flex;align-items:center;justify-content:center}

/* cta */
.cta h2{font-size:37px;font-weight:700;color:#fff;text-transform:uppercase}
.cta p{margin:12px auto 0;width:600px;font-size:14.5px;line-height:25px;color:#fff}

/* faq */
.faq{left:176px;width:848px;height:64px;background:#fff;border-left:3px solid var(--pink);box-shadow:0 2px 10px rgba(0,0,0,.07);display:flex;align-items:center;justify-content:space-between;padding:0 20px 0 22px;font-size:14.5px;font-weight:500}
.faq.open{height:111px;border:1.5px solid var(--pink);border-left:3px solid var(--pink);display:block;padding:20px 20px 0 22px}
.faq.open p{margin-top:8px;font-size:12px;line-height:22px;color:#666;font-weight:400}
.faq.open svg{position:absolute;right:20px;top:20px}
.totop{left:1097px;top:4583px;width:42px;height:42px;border-radius:50%;background:var(--pink);display:flex;align-items:center;justify-content:center}

/* footer */
.footer{left:0;top:4640px;width:1200px;height:389px}
.f-logo{left:140px;top:4733px;width:132px;height:130px;background:var(--pink);border:3px solid #f48aa6;display:flex;align-items:center;justify-content:center;text-align:center;font-weight:700;color:#fff;font-size:17px;line-height:1.2}
.socials{left:140px;top:4880px;display:flex;gap:8px}
.socials span{width:26px;height:26px;border-radius:50%;border:1.5px solid var(--yellow)}
.fcol{position:absolute;top:4733px;color:#fff;font-size:12.5px}
.fcol h4{font-size:15px;font-weight:500;margin-bottom:18px}
.fcol li{list-style:none;line-height:24.5px}
.contact-row{display:flex;gap:16px;margin-bottom:14px;line-height:19px}
.news input{display:block;width:256px;height:36px;border-radius:6px;border:none;padding:0 12px;font-family:inherit;font-size:12px;margin-top:16px}
.subscribe{margin-top:14px;width:142px;height:36px;background:var(--pink);border-radius:6px;color:#fff;font-size:14.5px;font-weight:600;display:flex;align-items:center;justify-content:center;box-shadow:4px 4px 0 #f48aa6}
.copy{left:0;top:4972px;width:1200px;text-align:center;color:#fff;font-size:12px}
</style>
</head>
<body>

<!-- top bar -->
<div class="abs topbar">
  <span style="left:667px"><svg width="14" height="14" viewBox="0 0 24 24"><path d="M6.6 10.8a15 15 0 0 0 6.6 6.6l2.2-2.2a1 1 0 0 1 1-.25 11 11 0 0 0 3.6.6 1 1 0 0 1 1 1V20a1 1 0 0 1-1 1A17 17 0 0 1 3 4a1 1 0 0 1 1-1h3.5a1 1 0 0 1 1 1 11 11 0 0 0 .6 3.6 1 1 0 0 1-.25 1z" fill="#222"/></svg>(044) 555 0142</span>
  <span style="left:808px"><svg width="15" height="15" viewBox="0 0 24 24"><path d="M2 11 22 3l-5 18-5-7z" fill="#222"/></svg>info@tiny-threaddays.ch</span>
  <span style="left:996px">Eng ▾ <svg width="20" height="14"><rect width="20" height="14" fill="#2a3f8f"/><path d="M0 0 20 14M20 0 0 14" stroke="#fff" stroke-width="3"/><path d="M0 0 20 14M20 0 0 14" stroke="#c8102e" stroke-width="1"/><path d="M10 0v14M0 7h20" stroke="#fff" stroke-width="4"/><path d="M10 0v14M0 7h20" stroke="#c8102e" stroke-width="2"/></svg></span>
</div>

<!-- nav -->
<div class="abs nav"></div>
<div class="abs brand">Tiny-<br>Thread<br>Days</div>
<nav class="menu">
  <a class="active" style="left:405px">HOME</a>
  <a style="left:479px">ABOUT US</a>
  <a style="left:576px">CAMPS</a>
  <a style="left:656px">HOW IT WORKS</a>
  <a style="left:785px">FAQ</a>
  <a style="left:846px">CONTACT US</a>
</nav>
<div class="abs btn-book">Book Now</div>

<!-- hero -->
<div class="abs hero-photo" role="img" aria-label="Photo of a smiling instructor at a sewing machine surrounded by children in a sewing workshop"></div>
<div class="abs hero-box">
  <h1>Creative Sewing<br>Holidays for Kids</h1>
  <p>Professional instruction in small groups. Multilingual support. Real results. Ages 9–14 in Zurich.</p>
  <div class="hero-btn">View Upcoming Camps</div>
</div>
<svg class="abs" style="left:140px;top:238px" width="112" height="40"><path d="M3 40V3h109" fill="none" stroke="#f2b51c" stroke-width="5"/></svg>
<svg class="abs" style="left:486px;top:460px" width="112" height="106"><path d="M0 103h109V0" fill="none" stroke="#f2b51c" stroke-width="5"/></svg>
<div class="abs scroll-dot"><svg width="18" height="30" viewBox="0 0 18 30"><rect x="2" y="1" width="14" height="22" rx="7" fill="none" stroke="#e8507a" stroke-width="1.8"/><path d="M9 6v6" stroke="#e8507a" stroke-width="1.8"/><path d="M5 26l4 3 4-3" fill="none" stroke="#e8507a" stroke-width="1.5"/></svg></div>

<!-- about -->
<svg class="abs" style="left:140px;top:806px" width="422" height="422" viewBox="0 0 422 422" role="img" aria-label="Collage of photos showing girls sewing and cutting fabric">
  <path d="M204 0A204 204 0 0 0 50 70V204H204Z" fill="#d9c4b2"/>
  <path d="M0 218H204V422A204 204 0 0 1 0 218Z" fill="#c9cdd6"/>
  <path d="M218 218H422A204 204 0 0 1 218 422Z" fill="#cfc3bd"/>
  <path d="M238 36A168 168 0 0 1 392 190H238Z" fill="#e8507a"/>
  <path d="M238 14A190 190 0 0 1 392 190" fill="none" stroke="#f2b51c" stroke-width="26" transform="translate(6 0)"/>
  <circle cx="211" cy="211" r="30" fill="#f2b51c"/>
  <circle cx="211" cy="211" r="23" fill="#fff"/>
  <circle cx="211" cy="211" r="14" fill="#2aa8dc"/>
  <path d="M211 218l-6-6a3.5 3.5 0 0 1 6-4 3.5 3.5 0 0 1 6 4z" fill="#fff"/>
</svg>
<div class="abs about-text">
  <div class="label">About our camps</div>
  <div class="heading">Learning with fun <em>&amp; Structure</em></div>
  <p>At Tiny-ThreadDays, we believe in nurturing creativity while having fun. Our experienced instructors create a safe, inspiring environment where children can explore their creative potential.</p>
  <p>With over 10 years of experience in teaching children sewing, tailoring, and design, Lena and Mara guide young talents through a creative week of vacation – with real results: self-sewn pieces, new friends, and lots of pride.</p>
  <p>At the last day, the children show off their success, their own sewn unique pieces, in a sympathetic fashion show.</p>
</div>
<div class="person" style="left:599px"><div class="avatar" role="img" aria-label="Portrait of Lena"></div><div><b>Lena</b><small>Sewing Expert</small></div></div>
<div class="person" style="left:817px"><div class="avatar" role="img" aria-label="Portrait of Mara"></div><div><b>Mara</b><small>Design Specialist</small></div></div>

<!-- how it works -->
<svg class="abs" style="left:0;top:1300px" width="1200" height="550" viewBox="0 0 1200 550" preserveAspectRatio="none">
  <path d="M0 40C200 10 350 70 600 40S1000 0 1200 30V520C1000 480 850 550 600 520S200 490 0 520Z" fill="#e9f5fb"/>
</svg>
<div class="abs center label" style="top:1432px">How our camps work</div>
<div class="abs center heading" style="top:1462px">Creative holiday camps for young <em>sewing Champs!</em></div>
<div class="abs how-cards">
  <div class="how-card"><span class="num">01</span>
    <svg class="step-icon" width="40" height="36"><path d="M6 32 30 6M24 4l10 10M10 20c6 4 12 4 16 0" fill="none" stroke="#e8507a" stroke-width="1.8"/></svg>
    <h3>Project Selection</h3><p>Your child chooses their own model based on previously produced clothing items and sewing patterns.</p></div>
  <div class="how-card"><span class="num">02</span>
    <svg class="step-icon" width="40" height="36"><rect x="4" y="10" width="32" height="20" rx="3" fill="none" stroke="#e8507a" stroke-width="1.8"/><path d="M4 17h32M4 23h32M12 10V5M28 10V5" stroke="#e8507a" stroke-width="1.8"/></svg>
    <h3>Fabric selection</h3><p>High-quality fabrics are available.</p></div>
  <div class="how-card"><span class="num">03</span>
    <svg class="step-icon" width="40" height="36"><path d="M4 30h32M8 30V10h24v12H16v8M22 22v6" fill="none" stroke="#e8507a" stroke-width="1.8"/></svg>
    <h3>Sewing machine</h3><p>Learn how to use a sewing machine</p></div>
  <div class="how-card"><span class="num">04</span>
    <svg class="step-icon" width="40" height="36"><path d="M8 6h24l-8 12v14h-8V18z" fill="none" stroke="#e8507a" stroke-width="1.8"/></svg>
    <h3>Sewing &amp; refining</h3><p>Step by step to the goal with professional guidance</p></div>
  <div class="how-card"><span class="num">05</span>
    <svg class="step-icon" width="40" height="36"><path d="M14 4l-10 8 5 6 4-3v17h16V15l4 3 5-6-10-8c-2 4-12 4-14 0z" fill="none" stroke="#e8507a" stroke-width="1.8"/></svg>
    <h3>Showtime!</h3><p>Fashion show or photo shoot at the end of the week</p></div>
</div>

<!-- why -->
<div class="abs center label" style="top:1939px">Why parents choose us</div>
<div class="abs center heading" style="top:1970px">Why families love Tiny-ThreadDays sewing <em>camps</em></div>
<div class="abs why-ring"></div>
<div class="abs why-core">Tiny-<br>ThreadDays</div>

<div class="why-item left" style="right:787px;top:2051px"><span>Small groups &amp;<br>personalized attention</span><div class="ico y"><svg width="32" height="32" viewBox="0 0 32 32"><path d="M6 6l9 9M15 8v7H8M26 26l-9-9M17 24v-7h7" fill="none" stroke="#fff" stroke-width="2.4"/></svg></div></div>
<div class="why-item left" style="right:811px;top:2174px"><span>Multilingual supervision<br>(DE / EN / IT)</span><div class="ico b"><svg width="32" height="32" viewBox="0 0 32 32"><path d="M4 8h14M11 5v3M7 8c1 5 5 9 9 10M15 8c-1 5-5 9-9 10M17 28l5-12 5 12M19 24h6" fill="none" stroke="#fff" stroke-width="2"/></svg></div></div>
<div class="why-item left" style="right:787px;top:2295px"><span>Pick-up Service from the<br>Main-Station</span><div class="ico p"><svg width="26" height="30" viewBox="0 0 26 30"><path d="M13 2a9 9 0 0 0-9 9c0 7 9 17 9 17s9-10 9-17a9 9 0 0 0-9-9z" fill="#fff"/><circle cx="13" cy="11" r="3.5" fill="#e8507a"/></svg></div></div>

<div class="why-item" style="left:772px;top:2050px"><div class="ico b"><svg width="34" height="34" viewBox="0 0 24 24"><path d="M12 3l2.7 5.6 6.1.9-4.4 4.3 1 6.1L12 17l-5.4 2.9 1-6.1L3.2 9.5l6.1-.9z" fill="none" stroke="#fff" stroke-width="1.6"/></svg></div><span>Encouragement of creativity,<br>self-confidence, and fine<br>motor skills</span></div>
<div class="why-item" style="left:798px;top:2174px"><div class="ico p"><svg width="30" height="32" viewBox="0 0 24 26"><path d="M12 2l9 4v7c0 6-4 10-9 11-5-1-9-5-9-11V6z" fill="none" stroke="#fff" stroke-width="1.8"/><path d="M8 13l3 3 5-6" fill="none" stroke="#fff" stroke-width="1.8"/></svg></div><span>Safe, loving environment in<br>Zurich, various places easy<br>to reach</span></div>
<div class="why-item" style="left:772px;top:2296px"><div class="ico y"><svg width="32" height="32" viewBox="0 0 32 32"><path d="M4 10h24M4 16h24M4 22h24M10 4v24M16 4v24M22 4v24" stroke="#fff" stroke-width="1.8"/></svg></div><span>High-quality fabrics &amp; top-<br>quality sewing machines<br>(Swiss-made)</span></div>
<div class="abs divider"></div>

<!-- camps -->
<div class="abs center label" style="top:2524px">Our upcoming camps</div>
<div class="abs center heading" style="top:2556px">Multilingual creativity, made just <em>for kids</em></div>

<article class="camp" style="left:140px">
  <div class="pic" role="img" aria-label="Photo of children sewing around a table with their instructor" style="background:linear-gradient(135deg,#b9a697,#d8c9bb 55%,#8d7a6e)"></div>
  <h3>Spring Sewing Camp</h3>
  <p>Join us for a creative week during spring break! Children will learn sewing basics and create their own spring-themed projects.</p>
  <dl><dt>Age:</dt><dd>09 to 14</dd><dt>Total:</dt><dd>200 Kids</dd><dt>Date:</dt><dd>21 Oct,2025</dd><dt>Duration:</dt><dd>06 Days</dd></dl>
</article>
<article class="camp" style="left:458px">
  <div class="pic" role="img" aria-label="Photo of children running through a sunny park" style="background:linear-gradient(160deg,#7f9a4d,#b7c97a 45%,#5f7a3a)"></div>
  <h3>Summer Fashion Camp</h3>
  <p>Our popular summer program where kids design and create their own summer wardrobe items in a fun, supportive environment.</p>
  <dl><dt>Age:</dt><dd>09 to 14</dd><dt>Total:</dt><dd>200 Kids</dd><dt>Date:</dt><dd>07 Jul,2025</dd><dt>Duration:</dt><dd>06 Days</dd></dl>
</article>
<article class="camp" style="left:776px">
  <div class="pic" role="img" aria-label="Photo of girls working at sewing machines in a bright studio" style="background:linear-gradient(135deg,#e6e2dc,#c9bfb6 50%,#a89c93)"></div>
  <h3>Autumn Creative Camp</h3>
  <p>Get ready for cooler weather by creating cozy autumn accessories and clothing items in this creative camp Autumn Creative Camp.</p>
  <dl><dt>Age:</dt><dd>09 to 14</dd><dt>Total:</dt><dd>200 Kids</dd><dt>Date:</dt><dd>21 Oct,2025</dd><dt>Duration:</dt><dd>06 Days</dd></dl>
</article>
<div class="abs pill" style="left:517px;top:3016px;background:var(--pink);color:#fff">View All Camps<i style="background:#fff"><svg width="12" height="12"><path d="M2 10l8-8M4 2h6v6" fill="none" stroke="#e8507a" stroke-width="1.8"/></svg></i></div>

<!-- cta -->
<svg class="abs" style="left:0;top:3130px" width="1200" height="400" viewBox="0 0 1200 400" preserveAspectRatio="none">
  <path d="M0 40C250 80 420 0 640 30S1000 60 1200 10V360C1000 400 800 330 560 370S200 390 0 350Z" fill="#3db4e2"/>
</svg>
<div class="abs center cta" style="top:3252px">
  <h2>Ready for a creative adventure?</h2>
  <p>Spaces are limited to 8 children per camp to ensure personalized attention. Book now to secure your child's spot!</p>
</div>
<div class="abs pill" style="left:517px;top:3398px;background:#fff;color:var(--blue)">View All Camps<i style="background:var(--blue)"><svg width="12" height="12"><path d="M2 10l8-8M4 2h6v6" fill="none" stroke="#fff" stroke-width="1.8"/></svg></i></div>

<!-- faq -->
<div class="abs center label" style="top:3627px">Frequently asked questions</div>
<div class="abs center heading" style="top:3658px">Everything you need to know about <em>our camps</em></div>

<div class="abs faq open" style="top:3717px">Does my child need any prior knowledge?
  <p>We welcome children aged 9-14 years. This age range ensures that participants have the fine motor skills needed for sewing while still being excited about creative projects.</p>
  <svg width="14" height="9"><path d="M1 8l6-6 6 6" fill="none" stroke="#777" stroke-width="1.6"/></svg>
</div>
<div class="abs faq" style="top:3848px">How does the pick-up service work?<svg width="14" height="9"><path d="M1 1l6 6 6-6" fill="none" stroke="#777" stroke-width="1.6"/></svg></div>
<div class="abs faq" style="top:3929px">How many items of clothing are produced?<svg width="14" height="9"><path d="M1 1l6 6 6-6" fill="none" stroke="#777" stroke-width="1.6"/></svg></div>
<div class="abs faq" style="top:4010px">What should my child bring to camp?<svg width="14" height="9"><path d="M1 1l6 6 6-6" fill="none" stroke="#777" stroke-width="1.6"/></svg></div>
<div class="abs faq" style="top:4091px">What are the camp hours?<svg width="14" height="9"><path d="M1 1l6 6 6-6" fill="none" stroke="#777" stroke-width="1.6"/></svg></div>
<div class="abs faq" style="top:4172px">We offer pick-up from Zurich Main Station at times. Parents can arrange this during booking<svg width="14" height="9"><path d="M1 1l6 6 6-6" fill="none" stroke="#777" stroke-width="1.6"/></svg></div>
<div class="abs faq" style="top:4253px">What is your cancellation policy?<svg width="14" height="9"><path d="M1 1l6 6 6-6" fill="none" stroke="#777" stroke-width="1.6"/></svg></div>
<div class="abs faq" style="top:4334px">How many items of clothing are produced?<svg width="14" height="9"><path d="M1 1l6 6 6-6" fill="none" stroke="#777" stroke-width="1.6"/></svg></div>
<div class="abs faq" style="top:4415px">Each child completes their own unique clothing item during the week<svg width="14" height="9"><path d="M1 1l6 6 6-6" fill="none" stroke="#777" stroke-width="1.6"/></svg></div>
<div class="abs faq" style="top:4496px">What safety measures are in place?<svg width="14" height="9"><path d="M1 1l6 6 6-6" fill="none" stroke="#777" stroke-width="1.6"/></svg></div>
<div class="abs totop"><svg width="18" height="12"><path d="M2 10l7-7 7 7" fill="none" stroke="#fff" stroke-width="2.4"/></svg></div>

<!-- footer -->
<svg class="abs footer" viewBox="0 0 1200 389" preserveAspectRatio="none">
  <path d="M0 20C150 50 300 0 500 25S850 45 1000 15 1150 10 1200 22V389H0Z" fill="#1e2a5a"/>
  <path d="M0 32C150 62 300 12 500 37S850 57 1000 27 1150 22 1200 34V389H0Z" fill="#3a2a6c"/>
</svg>
<div class="abs f-logo">Tiny-<br>Thread<br>Days</div>
<div class="abs socials"><span></span><span></span><span></span><span></span></div>
<div class="fcol" style="left:350px"><h4>Quick Links</h4><ul><li>Home</li><li>About Us</li><li>Camps</li><li>How It Works</li><li>Faq</li><li>Contact Us</li></ul></div>
<div class="fcol" style="left:520px"><h4>Contact Details</h4>
  <div class="contact-row"><svg width="18" height="20" viewBox="0 0 26 30"><path d="M13 2a9 9 0 0 0-9 9c0 7 9 17 9 17s9-10 9-17a9 9 0 0 0-9-9z" fill="#fff"/></svg><span>12 Atelierweg,<br>8005 Zurich, Switzerland</span></div>
  <div class="contact-row"><svg width="18" height="18" viewBox="0 0 24 24"><path d="M6.6 10.8a15 15 0 0 0 6.6 6.6l2.2-2.2a1 1 0 0 1 1-.25 11 11 0 0 0 3.6.6 1 1 0 0 1 1 1V20a1 1 0 0 1-1 1A17 17 0 0 1 3 4a1 1 0 0 1 1-1h3.5a1 1 0 0 1 1 1 11 11 0 0 0 .6 3.6 1 1 0 0 1-.25 1z" fill="#fff"/></svg><span>Phone<br>(044) 555 0142</span></div>
  <div class="contact-row"><svg width="18" height="18" viewBox="0 0 24 24"><path d="M2 11 22 3l-5 18-5-7z" fill="#fff"/></svg><span>Email<br>info@tiny-threaddays.ch</span></div>
</div>
<div class="fcol news" style="left:800px"><h4>Newsletter Sign Up</h4>
  <div style="line-height:19px">Subscribe to our newsletter to get the<br>latest update to your inbox</div>
  <input type="text" placeholder="Email address">
  <div class="subscribe">SUBSCRIBE</div>
</div>
<div class="abs copy">© 2025 Tiny-ThreadDays. All Rights Reserved.</div>

</body>
</html>
```